Open Now Poster for Retail Shop windows.

To design a poster to be printed to put on the windows of our retail stores to tell customers that we are open. Size is to be 590mm W x 840mm H supplied as a pdf. Design should incorporate our logo as well as other elements which indicate the style of our shop which is Womens Beach, Resort & Casual Clothing, Swimwear and Accessories. I would like the design to incorporate the words "Open Now" in some form in large lettering. I would also like the poster to be timeless and able to be used for other wording, so no images would be preferable.

Target Market(s)

Womens Beach, Resort & Casual Clothing, Swimwear and Accessories

Industry/Entity Type

Retail

Colors
e34297

Requirements
Must have
• words "Open Now". as well as our logo.

```html
<!DOCTYPE html>
<html lang="en">
<head>
<meta charset="utf-8">
<title>Sea Lark – Open Now Window Poster</title>
<link rel="stylesheet" href="https://fonts.googleapis.com/css2?family=Exo+2:wght@500;600;700&display=swap">
<style>
  :root {
    --brand-pink: #e3007f;
    --ink: #1c1c1c;
    --paper: #f1f1f1;
    --paper-edge: #e4e4e4;
    --white: #ffffff;
    --ring-grey: #c9c9c9;
    --icon-fill: #ececec;
  }
  html, body {
    margin: 0;
    padding: 0;
    overflow: hidden;
    background: var(--white);
  }
  .poster {
    position: relative;
    width: 960px;
    height: 1200px;
    overflow: hidden;
    font-family: "Exo 2", "Arial", sans-serif;
    background: radial-gradient(ellipse at 50% 45%, var(--white) 0%, var(--paper) 60%, var(--paper-edge) 100%);
  }
  .poster-shapes {
    position: absolute;
    inset: 0;
  }
  .brand-name {
    position: absolute;
    top: 40px;
    left: 0;
    width: 100%;
    margin: 0;
    text-align: center;
    font-size: 96px;
    line-height: 1;
    font-weight: 600;
    color: var(--brand-pink);
    letter-spacing: 1px;
  }
  .headline {
    position: absolute;
    left: 0;
    width: 100%;
    margin: 0;
    text-align: center;
    line-height: 1;
    font-weight: 600;
  }
  .headline-open {
    top: 258px;
    font-size: 310px;
    color: var(--brand-pink);
    letter-spacing: 2px;
  }
  .headline-now {
    top: 522px;
    font-size: 252px;
    color: var(--ink);
    letter-spacing: 2px;
  }
  .range-list {
    position: absolute;
    top: 1000px;
    left: 0;
    width: 100%;
    display: flex;
    margin: 0;
    padding: 0;
    list-style: none;
  }
  .range-item {
    flex: 1;
    text-align: center;
    color: var(--white);
    font-size: 25px;
    line-height: 1.3;
    font-weight: 600;
    letter-spacing: 0.5px;
  }
  .web-address {
    position: absolute;
    top: 1128px;
    left: 0;
    width: 100%;
    margin: 0;
    text-align: center;
    font-size: 44px;
    line-height: 1;
    font-weight: 700;
    color: var(--white);
    letter-spacing: 1px;
  }
</style>
</head>
<body>
<main class="poster">
  <svg class="poster-shapes" width="960" height="1200" viewBox="0 0 960 1200" aria-hidden="false">
    <!-- header band -->
    <path class="header-band" d="M0 0 H960 V162 Q470 300 0 127 Z" fill="var(--white)"/>
    <path class="header-rule" d="M0 127 Q470 300 960 162" fill="none" stroke="var(--brand-pink)" stroke-width="4"/>

    <!-- footer band -->
    <path class="footer-band" d="M0 1005 Q430 900 960 985 V1200 H0 Z" fill="var(--brand-pink)"/>
    <path class="footer-rule" d="M0 1120 Q240 985 560 968 Q800 958 960 1040" fill="none" stroke="var(--ink)" stroke-width="4"/>

    <!-- range dividers -->
    <g class="range-dividers" stroke="var(--white)" stroke-width="3">
      <line x1="312" y1="955" x2="312" y2="1080"/>
      <line x1="625" y1="955" x2="625" y2="1080"/>
    </g>
    <g class="range-dividers-notch" fill="var(--white)">
      <path d="M312 1012 l7 6 l-7 6 Z"/>
      <path d="M625 1012 l7 6 l-7 6 Z"/>
    </g>

    <!-- range badges -->
    <g class="range-badge">
      <circle cx="152" cy="886" r="74" fill="var(--ring-grey)"/>
      <circle cx="152" cy="880" r="72" fill="var(--white)"/>
      <circle cx="152" cy="880" r="60" fill="none" stroke="var(--brand-pink)" stroke-width="5"/>
      <circle cx="152" cy="880" r="50" fill="var(--icon-fill)" role="img" aria-label="Bikini icon"/>
    </g>
    <g class="range-badge">
      <circle cx="468" cy="886" r="74" fill="var(--ring-grey)"/>
      <circle cx="468" cy="880" r="72" fill="var(--white)"/>
      <circle cx="468" cy="880" r="60" fill="none" stroke="var(--brand-pink)" stroke-width="5"/>
      <circle cx="468" cy="880" r="50" fill="var(--icon-fill)" role="img" aria-label="T-shirt icon"/>
    </g>
    <g class="range-badge">
      <circle cx="785" cy="886" r="74" fill="var(--ring-grey)"/>
      <circle cx="785" cy="880" r="72" fill="var(--white)"/>
      <circle cx="785" cy="880" r="60" fill="none" stroke="var(--brand-pink)" stroke-width="5"/>
      <circle cx="785" cy="880" r="50" fill="var(--icon-fill)" role="img" aria-label="Sun hat and flip-flops icon"/>
    </g>
  </svg>

  <h1 class="brand-name">sea lark</h1>

  <p class="headline headline-open">OPEN</p>
  <p class="headline headline-now">NOW</p>

  <ul class="range-list">
    <li class="range-item">Womens<br>Beach Clothing</li>
    <li class="range-item">Resort &amp;<br>Casual Clothing</li>
    <li class="range-item">Swimwear and<br>Accessories</li>
  </ul>

  <p class="web-address">www.sealark.com</p>
</main>
</body>
</html>
```